Business Card Design Project for a Restaurant/Wine Bar

New, fresh business card design for Brevenna Wine Bar & Restaurant, Bandon, Oregon. We are an established restaurant on the Oregon coast featuring "Italian coastal cuisine."

"Brevenna" means bay leaf in Italian. We aren't sure if we would like our logo on the card or not, but if you have something interesting that uses it, then please do so. The basic information is essential - full restaurant name, address, phone and website (do not use www). The font on our menu and wine list may give you some sort of an idea of our style.

One-sided card needed as we often use the backside to write down various types of info for customers.
Updates

After seeing a few submissions, we would like to see what designers can come up with-using the logo, just the leaf, or none at all. Sky is the limit as long as our full restaurant name, address, phone and website (please leave out www) are there. Please contact us if questions!

I appreciate all of your designs! Our deadline is next week, but I will continue to give feedback on designs as I can. This is our busiest season, so my co-owner/chef/husband, won't have time to look at the designs for awhile. When he does, we can make our decision.

cheers,
Maren

Target Market(s)

Fine dining/wine crowd. Would like something simple and elegant, but not pretentious or stuffy. Brevenna means bay laurel (bay leaf) in Italian (please see our logo).

Industry/Entity Type

Restaurant

Requirements
Must have
• Full Name of Restaurant: Brevenna Wine Bar & Restaurant
Address: 812 4th Ave NW, Coveton, Oregon 97499
Phone: 541.555.0172
website: brevennawinebar.example (do not use www)
Should not have
• Loud colors.

```html
<!DOCTYPE html>
<html lang="en">
<head>
<meta charset="utf-8">
<title>Brevenna Wine Bar &amp; Restaurant – Business Card</title>
<link rel="stylesheet" href="https://fonts.googleapis.com/css2?family=PT+Sans:wght@400;700&display=swap">
<style>
  :root {
    --backdrop: #e6e3dd;
    --card: #ffffff;
    --ink: #1b1b1b;
    --sage: #9c9d7d;
    --rule: #1b1b1b;
    --on-sage: #ffffff;
  }
  * { margin: 0; padding: 0; box-sizing: border-box; }
  html, body {
    width: 1200px;
    height: 744px;
    overflow: hidden;
    background: var(--backdrop);
    font-family: "PT Sans", Arial, sans-serif;
  }
  .card {
    position: absolute;
    left: 40px;
    top: 40px;
    width: 1120px;
    height: 664px;
    background: var(--card);
    border-radius: 44px;
    overflow: hidden;
    box-shadow: 0 6px 18px rgba(0,0,0,0.12);
  }
  .card-band {
    position: absolute;
    inset: 0;
    width: 100%;
    height: 100%;
  }
  .brand-name {
    position: absolute;
    top: 118px;
    left: 0;
    width: 100%;
    text-align: center;
    font-weight: 700;
    font-size: 128px;
    letter-spacing: 4px;
    color: var(--ink);
    line-height: 1;
  }
  .restaurant-title {
    position: absolute;
    top: 488px;
    left: 0;
    width: 100%;
    text-align: center;
    font-weight: 700;
    font-size: 36px;
    line-height: 48px;
    color: var(--on-sage);
  }
  .contact,
  .address {
    position: absolute;
    top: 560px;
    color: var(--on-sage);
    font-size: 26px;
    line-height: 38px;
    font-weight: 400;
    font-style: normal;
  }
  .contact { left: 150px; }
  .address { left: 640px; }
  .contact-line {
    display: flex;
    align-items: center;
    gap: 10px;
  }
  .contact-icon {
    width: 22px;
    height: 22px;
    flex: none;
  }
</style>
</head>
<body>
  <main class="card">
    <svg class="card-band" viewBox="0 0 1120 664" aria-hidden="true">
      <path d="M0 478 Q520 372 1120 438 L1120 664 L0 664 Z" fill="var(--sage)"/>
      <path d="M0 450 Q520 352 1120 418" fill="none" stroke="var(--rule)" stroke-width="2.5"/>
    </svg>

    <h1 class="brand-name">Brevenna</h1>

    <h2 class="restaurant-title">Brevenna Wine Bar &amp; Restaurant</h2>

    <div class="contact">
      <p class="contact-line">
        <svg class="contact-icon" viewBox="0 0 24 24" aria-hidden="true">
          <path d="M6.6 10.8a15 15 0 0 0 6.6 6.6l2.2-2.2a1 1 0 0 1 1-.25 11.4 11.4 0 0 0 3.6.57 1 1 0 0 1 1 1V20a1 1 0 0 1-1 1A17 17 0 0 1 3 4a1 1 0 0 1 1-1h3.5a1 1 0 0 1 1 1c0 1.25.2 2.45.57 3.57a1 1 0 0 1-.25 1z" fill="currentColor"/>
        </svg>
        541.555.0172
      </p>
      <p class="contact-line">
        <svg class="contact-icon" viewBox="0 0 24 24" aria-hidden="true">
          <circle cx="12" cy="12" r="9.5" fill="none" stroke="currentColor" stroke-width="2"/>
          <ellipse cx="12" cy="12" rx="4" ry="9.5" fill="none" stroke="currentColor" stroke-width="1.6"/>
          <line x1="2.5" y1="12" x2="21.5" y2="12" stroke="currentColor" stroke-width="1.6"/>
        </svg>
        brevennawinebar.example
      </p>
    </div>

    <address class="address">
      812 4th Ave NW, Coveton,<br>
      Oregon 97499
    </address>
  </main>
</body>
</html>
```